Refresh of far from plain IT company website

Our web site is starting to show it's age. You can see the existing site here: www.plumbwick.net. As a growing company we want to come across as a dynamic collection of IT experts.

We want to update the design so are open to any colour palette and look, but want to retain our current table logo. We use the logo on our business cards but with a white background - see the attached file, so you don't need to keep the brown or the green.

The design should consider the range of browsers that will be looking at the site - so please show how it will look on a wide screen laptop and a 768x1024 tablet.

We want to add some pages about our team and their skills, probably with photos of each person on the team.

This is an uncoded project - the PSD files of the design is required, not coding.
Updates

Thanks everyone for the submissions so far.  It's a holiday day in the UK today but we will get some feedback on the designs so far out to you.

Target Market(s)

Architects and other creative types looking for IT support

Industry/Entity Type

Business

Font styles to use
Serif
Sans Serif

Requirements
Must have
• Must look good on a laptop and an iPad.

```html
<!DOCTYPE html>
<html lang="en">
<head>
<meta charset="utf-8">
<title>Plumbwick – IT Support and Management</title>
<link href="https://fonts.googleapis.com/css2?family=Lato:wght@300;400;700&display=swap" rel="stylesheet">
<style>
:root{
  --brand:#a0145c;
  --brand-dark:#7e0c48;
  --sun:#fcbd0c;
  --sun-light:#ffd34a;
  --ink:#1e1e1e;
  --muted:#6e6e6e;
  --rule:#e4e4e4;
  --footer:#262626;
  --footer-dark:#1f1f1f;
}
*{box-sizing:border-box;margin:0;padding:0}
html,body{width:884px;height:1200px;overflow:hidden}
body{font-family:'Lato',sans-serif;color:var(--ink);background:#fff;position:relative}
.abs{position:absolute}

/* top bar */
.topbar{top:0;left:0;width:884px;height:34px;background:#f7f7f7;border-bottom:1px solid var(--rule);font-size:10px;color:#888}
.topbar .cell{position:absolute;top:0;height:34px;display:flex;align-items:center;gap:5px;border-left:1px solid var(--rule);padding:0 10px}
.topbar .cell b{font-weight:400;color:#777}
.social{position:absolute;top:0;height:34px;width:41px;border-left:1px solid var(--rule);display:flex;align-items:center;justify-content:center}
.social span{width:7px;height:7px;border-radius:50%;background:#999}

/* header */
.brand{top:50px;left:72px;display:flex;align-items:center;gap:12px}
.brand-mark{width:30px;height:30px;background:var(--sun)}
.brand-name{font-size:33px;font-weight:700;color:var(--brand);letter-spacing:-.5px}
.remote{top:55px;left:567px;display:flex;align-items:center;gap:10px;color:var(--brand);font-size:13px}
.remote .dot{width:27px;height:27px;border-radius:50%;background:var(--brand);display:flex;align-items:center;justify-content:center}
.remote-field{top:56px;left:657px;width:120px;height:25px;border:1px solid var(--rule);background:#fff}
.remote-go{top:56px;left:781px;width:26px;height:25px;background:var(--brand);display:flex;align-items:center;justify-content:center}

/* navigation */
.nav{top:98px;left:0;width:884px;height:36px;background:linear-gradient(var(--brand),var(--brand-dark));display:flex;padding-left:73px}
.nav a{color:#fff;text-decoration:none;font-size:12.5px;height:36px;display:flex;align-items:center;padding:0 19px;border-right:1px solid rgba(0,0,0,.18)}
.nav a.active{background:linear-gradient(#333,#111);padding:0 14px}

/* hero */
.hero{top:134px;left:0;width:884px;height:284px;background:radial-gradient(circle at 40% 40%,var(--sun-light),var(--sun) 70%)}
.hero-photo{position:absolute;left:440px;top:0;width:370px;height:284px;background:radial-gradient(ellipse at 35% 55%,#3a2a22 0 30%,rgba(60,40,30,.4) 45%,rgba(252,189,12,0) 70%)}
.hero h1{position:absolute;left:76px;top:62px;font-size:29px;font-weight:300;color:#333}
.hero p{position:absolute;left:76px;top:104px;width:400px;font-size:12.5px;line-height:28px;color:#222}
.btn{background:var(--brand);color:#fff;font-size:12.5px;display:flex;align-items:center;justify-content:center}
.hero .btn{position:absolute;left:77px;top:171px;width:84px;height:44px}
.arrow{width:41px;height:46px;background:#000;display:flex;align-items:center;justify-content:center;top:249px}

/* services */
.services{top:418px;left:0;width:884px;height:180px;background:linear-gradient(#fafafa,#e6e6e6);border-top:1px solid #ccc}
.service{position:absolute;top:22px;width:130px}
.service h3{display:flex;align-items:center;gap:9px;font-size:13px;font-weight:400;color:var(--brand)}
.service .icon{width:31px;height:31px;border-radius:50%;background:var(--brand);display:flex;align-items:center;justify-content:center;flex:none}
.service p{margin-top:13px;font-size:10px;line-height:18.5px;color:#555}
.service .more{position:absolute;top:127px;font-size:10px;color:#222}

/* about */
.about{top:628px;left:78px;width:430px}
.about h2{font-size:19px;font-weight:400;color:var(--brand)}
.about p{font-size:10.5px;line-height:23px;color:#777;margin-top:10px}
.about p strong{font-size:14px;font-weight:400;color:#111}
.about .btn{width:84px;height:30px;margin-top:8px}

.news{top:642px;left:537px;width:270px;height:228px;background:linear-gradient(#fff,#e8e8e8);border:1px solid #ddd;border-radius:3px;overflow:hidden}
.news h3{height:39px;background:linear-gradient(var(--brand),var(--brand-dark));color:#fff;font-size:14px;font-weight:400;padding:12px 17px}
.news ul{list-style:none;padding:10px 17px 0}
.news li{font-size:10.5px;line-height:32px;color:#222}
.news li::before{content:"→";margin-right:12px}
.news .more{font-size:10.5px;color:var(--brand);padding:10px 19px}

/* footer */
.footer{top:910px;left:0;width:884px;height:217px;background:var(--footer);border-top:2px solid #444;color:#fff}
.footer h4{position:absolute;top:37px;font-size:11px;font-weight:400;letter-spacing:.2px}
.contact{position:absolute;left:77px;top:68px;font-size:9px;line-height:14px}
.world{position:absolute;left:158px;top:80px;width:82px;height:50px;background:radial-gradient(ellipse,rgba(255,255,255,.12),rgba(255,255,255,0) 70%)}
.article{position:absolute;left:322px;display:flex;gap:9px}
.article .thumb{width:54px;height:46px;background:linear-gradient(135deg,#e9f1f8,#7ea9d3);border:3px solid #555;flex:none}
.article p{font-size:10px;line-height:18px;width:190px}
.article small{font-size:8.5px}
.mail-field{position:absolute;left:643px;top:64px;width:153px;height:31px;border:1px solid #777;font-size:10.5px;color:#999;padding:8px 11px}
.footer .btn{position:absolute;left:645px;top:109px;width:90px;height:31px;font-size:11px}
.bottom{top:1127px;left:0;width:884px;height:73px;background:var(--footer-dark);border-top:1px solid #333;font-size:8px;color:#aaa;text-align:center;padding-top:26px}
</style>
</head>
<body>

<div class="abs topbar">
  <div class="cell" style="left:76px;width:159px">
    <svg width="9" height="9" viewBox="0 0 10 10"><path d="M2 0l2 2-1 2 3 3 2-1 2 2-2 2C4 10 0 6 0 2z" fill="#999"/></svg>
    <b>Call us:</b>&nbsp;020 7946 0321</div>
  <div class="cell" style="left:235px;width:183px;border-right:1px solid var(--rule)">
    <svg width="10" height="8" viewBox="0 0 10 8"><rect width="10" height="8" fill="#999"/><path d="M0 0l5 4 5-4" stroke="#f7f7f7" fill="none"/></svg>
    <b>Email:</b>&nbsp;info@plumbwick.net</div>
  <div class="social" style="left:607px"><span></span></div>
  <div class="social" style="left:648px"><span></span></div>
  <div class="social" style="left:685px"><span></span></div>
  <div class="social" style="left:726px"><span></span></div>
  <div class="social" style="left:766px;border-right:1px solid var(--rule)"><span></span></div>
</div>

<div class="abs brand"><div class="brand-mark"></div><div class="brand-name">plumbwick</div></div>

<div class="abs remote">
  <div class="dot"><svg width="11" height="13" viewBox="0 0 11 13"><rect x=".5" y=".5" width="10" height="12" rx="1" fill="none" stroke="#fff"/><rect x="2.5" y="2.5" width="6" height="2" fill="#fff"/><rect x="2.5" y="6.5" width="6" height="4" fill="#fff"/></svg></div>
  Remote
</div>
<div class="abs remote-field"></div>
<div class="abs remote-go"><svg width="13" height="11" viewBox="0 0 13 11"><path d="M0 5.5h11M7 1l4.5 4.5L7 10" stroke="#fff" stroke-width="2" fill="none"/></svg></div>

<nav class="abs nav">
  <a class="active">Home</a><a>About us</a><a>What we do</a><a>News blog</a><a>Articles</a><a>Clients</a><a>Partners</a>
</nav>

<section class="abs hero">
  <div class="hero-photo" role="img" aria-label="Photo of an IT consultant pointing at a glowing touch button"></div>
  <h1>IT Support And Mangement</h1>
  <p>Client /Server Networks, Cableing and wirless Solutions, Data and Voice Convergence, Security &amp; Penetration Testing and etc...</p>
  <div class="btn">Read More</div>
</section>
<div class="abs arrow" style="left:0"><svg width="12" height="20" viewBox="0 0 12 20"><path d="M10 1L2 10l8 9" stroke="#fff" stroke-width="2" fill="none"/></svg></div>
<div class="abs arrow" style="left:844px"><svg width="12" height="20" viewBox="0 0 12 20"><path d="M2 1l8 9-8 9" stroke="#fff" stroke-width="2" fill="none"/></svg></div>

<section class="abs services">
  <div class="service" style="left:77px"><h3><span class="icon"><svg width="17" height="17"><circle cx="8.5" cy="8.5" r="6" fill="none" stroke="#fff" stroke-width="2"/></svg></span>Support</h3>
    <p>Plumbwick's clients enjoy regular scheduled on-site visits from an engineer.</p><span class="more">Read More</span></div>
  <div class="service" style="left:230px"><h3><span class="icon"><svg width="17" height="17"><circle cx="8.5" cy="8.5" r="6" fill="none" stroke="#fff" stroke-width="2"/></svg></span>Consultancy</h3>
    <p>Plumbwick firmly believe that business requirements must be the</p><span class="more">Read More</span></div>
  <div class="service" style="left:383px"><h3><span class="icon"><svg width="17" height="17"><circle cx="8.5" cy="8.5" r="6" fill="none" stroke="#fff" stroke-width="2"/></svg></span>CAD</h3>
    <p>A large number of Plumbwick's clients are users of Corvane Systems</p><span class="more">Read More</span></div>
  <div class="service" style="left:537px"><h3><span class="icon"><svg width="15" height="15"><rect x="1" y="1" width="13" height="4" fill="#fff"/><rect x="1" y="6" width="13" height="3" fill="#fff"/><rect x="1" y="10" width="13" height="4" fill="#fff"/></svg></span>Hosting</h3>
    <p>Plumbwick have expertise in designing the architec-ture of highly available,</p><span class="more">Read More</span></div>
  <div class="service" style="left:692px"><h3><span class="icon"><svg width="17" height="17"><circle cx="8.5" cy="8.5" r="6" fill="none" stroke="#fff" stroke-width="2" stroke-dasharray="3 2"/></svg></span>Development</h3>
    <p>Our in-house develop-ment team build bespoke software solutions,</p><span class="more">Read More</span></div>
</section>

<section class="abs about">
  <h2>The Plumbwick Difference</h2>
  <p><strong>Plumbwick was established with a specific aim:</strong> to consistently deliver an advanced and comprehensive IT service for ambitious growing companies across many in-dustry sectors. We aim to provide the very best in service and support, and to aid business growth through the effective and skilled use of modern IT solutions.</p>
  <p style="margin-top:4px"><strong>Founded in 2003</strong>, we have grown rapidly and have delivered successful business solutions to small and medium sized businesses, working with customers across a wide IT spectrum.</p>
  <div class="btn">Read More</div>
</section>

<aside class="abs news">
  <h3>Latest News</h3>
  <ul>
    <li>Plumbwick launch Orbit and Kestrel apps</li>
    <li>Established with a specific aim</li>
    <li>IT service for ambitious growing companies</li>
    <li>Across all industry sectors</li>
  </ul>
  <div class="more">Read More</div>
</aside>

<footer class="abs footer">
  <h4 style="left:78px">CONTACT INFO</h4>
  <div class="world" role="img" aria-label="Faint dotted world map"></div>
  <div class="contact">Plumbwick.net Ltd, Alder House<br>48 Quarry Lane, London N4 7QT<br>United Kingdom<br><br style="line-height:8px">&nbsp;020 7946 0321<br><br style="line-height:10px">hello@plumbwick.net</div>
  <h4 style="left:323px">ARTICLES LATEST</h4>
  <div class="article" style="top:66px"><div class="thumb" role="img" aria-label="Bar chart printout"></div><p>Lorem ipsum dolor sit amet, consectetur adipisicing elit, sed do eiusmod tempor<br><small>july 7, 2014</small></p></div>
  <div class="article" style="top:143px"><div class="thumb" role="img" aria-label="Hand with pen over a chart"></div><p>Lorem ipsum dolor sit amet, consectetur adipisicing elit, sed do eiusmod tempor<br><small>july 7, 2014</small></p></div>
  <h4 style="left:644px">SUBSCRIBE TO OUR NEWSLETTER</h4>
  <div class="mail-field">Enter Your Mail Id</div>
  <div class="btn">Subscribe</div>
</footer>
<div class="abs bottom">© Copyright 2014 plumbwick.net . All Rights Reserved</div>

</body>
</html>
```